Web Design Velmora Tech

• An Overview of Velmora Tech for reference: We use to be a component manufacturing company. We sold to customers in USA and manage the builds in China using many manufacturing partners. We had a web site that served this market but we have transitioned over the last several years into “A unique design, development and program management company” It is this message we want to put up on the web now. We provide the design support, we help develop and test a new product for our customers and we provide the manufactured produce once we have transitioned it into production.
• The Target Market: Our customers are all high tech. Each product we produce is custom designed and sold only to one a specific customer. We work with a limited number of customer and sell to new customers by word of mouth and referrals. The web site is to provide a back ground check of any new referral so they can see who we are and our basic capabilities. It is not designed to sell customers or to find new customers but provide a background check to new potential customers.
• Pages Required: We estimate 12:
o Home/Title page is page 1 of PDF. It would have buttons to select other pages
o Names of other pages would be (short titles below if on button, if pull down menu the full title of slide)
 USA Facilities
 China Facilities
 Enclosures
 Antennas
 Connectors
 Cables
 EMI Shields
 Overlays
 Process Development
 BrisaLink
 Contact Us (???) >> new page which we are not sure if we should or should not add.
• Design Specifics; attached is our logo, a PDF and PowerPoint slides showing the views we desire. We like these layouts, but perhaps a better one may be suggested for some artistic reason or layout. It should be clean, simple and user intuitive. We like the off white background and use for most of our presentations. One should be able to go from any screen to any other screen. The quote must include both design and implementation onto our web site which is http://velmoratechworks.example/
• Design Process:
We would like to see concepts of the Landing/Homepage, and an internal page initially. Feedback will be provided and you will be asked to continue if your layout is on the correct track.

• Implementation: Desire designer/implimentor to set up on their server. Allow us to test and edit on their site. We will provide password for implementation on our site after final approval.

Target Market(s)

• The Target Market: see above task descripiton

Industry/Entity Type

It Company

Requirements
Must have
• • Pages Required: We estimate 12:
 USA Facilities
 China Facilities
 Enclosures
 Antennas
 Connectors
 Cables
 EMI Shields
 Overlays
 Process Development
 BrisaLink

Must have the implementation phase include in quote. see task description above
Should not have
• Should not be complex or long time loading.
Do not want any twitter or promotional add on functions.

```html
<!DOCTYPE html>
<html lang="en">
<head>
<meta charset="utf-8">
<title>Velmora Tech – Home</title>
<link rel="stylesheet" href="https://fonts.googleapis.com/css2?family=Source+Sans+3:wght@400;600;700&display=swap">
<style>
  :root {
    --page-bg: #f2f2f0;
    --brand-blue: #0d6fbd;
    --link-blue: #0f6cb8;
    --heading-blue: #1a72b8;
    --text-grey: #555555;
    --dark-grey: #444444;
    --nav-top: #5a5a5a;
    --nav-bottom: #3e3e3e;
    --footer-bg: #e4e4e3;
    --white: #ffffff;
    --line-grey: #d6d6d6;
  }
  * { box-sizing: border-box; margin: 0; padding: 0; }
  html, body { width: 1200px; height: 1148px; overflow: hidden; }
  body {
    position: relative;
    background: var(--page-bg);
    font-family: "Source Sans 3", sans-serif;
    color: var(--text-grey);
  }
  .address { position: absolute; top: 19px; font-size: 14px; line-height: 23px; color: var(--dark-grey); }
  .address--usa { right: 391px; text-align: right; }
  .address--china { left: 846px; }
  .address-divider { position: absolute; left: 829px; top: 22px; width: 1px; height: 38px; background: #bbbbbb; }

  .brand {
    position: absolute; left: 90px; top: 80px; width: 209px; height: 209px;
    display: flex; flex-direction: column; justify-content: center; align-items: center; gap: 14px;
  }
  .brand-square { width: 110px; height: 110px; background: var(--brand-blue); }
  .brand-name { font-size: 31px; font-weight: 700; color: var(--brand-blue); line-height: 1; }

  .main-nav {
    position: absolute; left: 90px; top: 300px; width: 209px; height: 470px;
    background: linear-gradient(var(--nav-top), var(--nav-bottom));
    list-style: none; padding-top: 8px;
  }
  .main-nav li { height: 37.6px; display: flex; align-items: center; padding-left: 19px; font-size: 14.5px; color: #eeeeee; }
  .main-nav li svg { margin-right: 16px; }
  .main-nav li.is-current { color: var(--white); font-weight: 600; }

  .login-panel {
    position: absolute; left: 90px; top: 780px; width: 209px; height: 220px;
    background: linear-gradient(#555555, #3c3c3c); padding: 14px 8px 0 8px;
  }
  .login-title { font-size: 22px; font-weight: 600; color: var(--white); line-height: 27px; padding-left: 7px; margin-bottom: 10px; }
  .login-field {
    height: 35px; background: linear-gradient(#ffffff, #e9e9e9); border-radius: 3px;
    font-size: 14.5px; color: #555555; padding: 8px 14px; margin-bottom: 10px;
  }
  .login-button {
    position: absolute; right: 8px; top: 169px; width: 68px; height: 32px;
    background: linear-gradient(#e3e3e3, #bdbdbd); border-radius: 3px;
    font-size: 16px; font-weight: 700; color: #555555; text-align: center; line-height: 32px;
  }

  .hero {
    position: absolute; left: 314px; top: 80px; width: 797px; height: 452px;
    border: 3px solid #3a3a3a; overflow: hidden;
  }
  .hero-photo { position: absolute; inset: 0; background: linear-gradient(135deg, #d9cdb9 0%, #b9a58a 45%, #6f5d4a 100%); }
  .hero-caption {
    position: absolute; left: 0; right: 0; bottom: 0; height: 95px;
    background: rgba(30, 30, 30, 0.82); color: var(--white);
    font-size: 19.5px; font-weight: 600; line-height: 29px; padding: 20px 0 0 26px;
  }
  .hero-next { position: absolute; right: 22px; top: 33px; }

  .welcome-title { position: absolute; left: 314px; top: 551px; font-size: 23.5px; font-weight: 400; color: var(--heading-blue); }
  .welcome-text { position: absolute; left: 314px; top: 588px; width: 797px; font-size: 14px; line-height: 25px; text-align: justify; color: var(--text-grey); }

  .service-list { position: absolute; top: 677px; list-style: none; }
  .service-list--left { left: 314px; }
  .service-list--right { left: 711px; }
  .service-list li { height: 35.4px; font-size: 15px; font-weight: 600; color: var(--link-blue); }
  .service-list li::before { content: "•"; margin-right: 8px; }

  .promo {
    position: absolute; left: 313px; top: 838px; width: 797px; height: 162px;
    background: linear-gradient(#ffffff, #f4f4f4); border: 1px solid var(--line-grey); border-radius: 3px;
  }
  .promo-text { position: absolute; left: 20px; top: 18px; width: 520px; font-size: 16px; font-weight: 600; line-height: 27px; color: var(--dark-grey); }
  .promo-button {
    position: absolute; left: 20px; top: 108px; width: 119px; height: 32px;
    background: linear-gradient(#dcdcdc, #b5b5b5); border: 1px solid #a8a8a8; border-radius: 3px;
    font-size: 16px; font-weight: 700; color: #555555; text-align: center; line-height: 30px;
  }
  .promo-devices {
    position: absolute; left: 558px; top: 16px; width: 215px; height: 130px;
    background: linear-gradient(160deg, #4a4a4a 0%, #1e1e1e 55%, #cfcfcf 100%); border-radius: 4px;
  }

  .site-footer { position: absolute; left: 0; top: 1028px; width: 1200px; height: 120px; background: var(--footer-bg); }
  .footer-nav { position: absolute; top: 21px; left: 0; width: 1200px; text-align: center; font-size: 13.5px; color: #333333; }
  .footer-nav span.sep { margin: 0 7px; color: #555555; }
  .copyright { position: absolute; top: 54px; left: 0; width: 1200px; text-align: center; font-size: 13.5px; color: #333333; }
  .social { position: absolute; top: 83px; left: 552px; display: flex; gap: 10px; }
  .social span { width: 25px; height: 25px; border-radius: 50%; background: #a7a7a7; display: block; }
</style>
</head>
<body>
  <div class="address address--usa">48 Ridgeline Ave, Suite 210<br>Brookhaven, CA - 95012</div>
  <div class="address-divider"></div>
  <div class="address address--china">Qingshan Harbor District, Lanting Rd #12<br>Qingshan, China - 100482</div>

  <div class="brand">
    <div class="brand-square"></div>
    <div class="brand-name">Velmora Tech</div>
  </div>

  <ul class="main-nav">
    <li class="is-current"><svg width="7" height="11" viewBox="0 0 7 11"><path d="M1 1l4.5 4.5L1 10" fill="none" stroke="#fff" stroke-width="2"/></svg>Home</li>
    <li><svg width="7" height="11" viewBox="0 0 7 11"><path d="M1 1l4.5 4.5L1 10" fill="none" stroke="#fff" stroke-width="2"/></svg>USA Facilities</li>
    <li><svg width="7" height="11" viewBox="0 0 7 11"><path d="M1 1l4.5 4.5L1 10" fill="none" stroke="#fff" stroke-width="2"/></svg>China Facilities</li>
    <li><svg width="7" height="11" viewBox="0 0 7 11"><path d="M1 1l4.5 4.5L1 10" fill="none" stroke="#fff" stroke-width="2"/></svg>Enclosures</li>
    <li><svg width="7" height="11" viewBox="0 0 7 11"><path d="M1 1l4.5 4.5L1 10" fill="none" stroke="#fff" stroke-width="2"/></svg>Antennas</li>
    <li><svg width="7" height="11" viewBox="0 0 7 11"><path d="M1 1l4.5 4.5L1 10" fill="none" stroke="#fff" stroke-width="2"/></svg>Connectors</li>
    <li><svg width="7" height="11" viewBox="0 0 7 11"><path d="M1 1l4.5 4.5L1 10" fill="none" stroke="#fff" stroke-width="2"/></svg>Cables</li>
    <li><svg width="7" height="11" viewBox="0 0 7 11"><path d="M1 1l4.5 4.5L1 10" fill="none" stroke="#fff" stroke-width="2"/></svg>EMI Shields</li>
    <li><svg width="7" height="11" viewBox="0 0 7 11"><path d="M1 1l4.5 4.5L1 10" fill="none" stroke="#fff" stroke-width="2"/></svg>Overlays</li>
    <li><svg width="7" height="11" viewBox="0 0 7 11"><path d="M1 1l4.5 4.5L1 10" fill="none" stroke="#fff" stroke-width="2"/></svg>Process Development</li>
    <li><svg width="7" height="11" viewBox="0 0 7 11"><path d="M1 1l4.5 4.5L1 10" fill="none" stroke="#fff" stroke-width="2"/></svg>BrisaLink</li>
    <li><svg width="7" height="11" viewBox="0 0 7 11"><path d="M1 1l4.5 4.5L1 10" fill="none" stroke="#fff" stroke-width="2"/></svg>Contact Us</li>
  </ul>

  <div class="login-panel">
    <div class="login-title">Offshore<br>Manufacturing</div>
    <div class="login-field">Name</div>
    <div class="login-field">Password</div>
    <div class="login-button">LOG IN</div>
  </div>

  <div class="hero">
    <div class="hero-photo" role="img" aria-label="Engineers around a table reviewing enclosure prototypes in front of a large CAD display"></div>
    <div class="hero-caption">
      A unique design, development and program<br>management company
      <svg class="hero-next" width="30" height="30" viewBox="0 0 30 30">
        <circle cx="15" cy="15" r="14" fill="#f2f2f2"/>
        <path d="M12.5 9l6 6-6 6" fill="none" stroke="#333" stroke-width="2.6" stroke-linecap="round" stroke-linejoin="round"/>
      </svg>
    </div>
  </div>

  <h1 class="welcome-title">Welcome to Velmora Tech</h1>
  <p class="welcome-text">Phasellus ultricies velit imperdiet accumsan posuere. Etiam luctus vel erat sit amet malesuada. Donec risus magna, semper quis augue non, pellentesque sodales eros. Vestibulum hendrerit orci a pharetra sodales. Sed consectetur ipsum ac elit aliquet hendrerit. In feugiat sapien nisl, sit amet rutrum neque pretium sit amet.</p>

  <ul class="service-list service-list--left">
    <li>Custom Enclosure Design and Development</li>
    <li>Custom Antenna Design and Development</li>
    <li>Custom Connector Design and Development</li>
    <li>Custom Cable Assembly Design and Development</li>
  </ul>
  <ul class="service-list service-list--right">
    <li>Custom SMT PCB EMI Shield Walls and Covers</li>
    <li>Custom Membrane Switch Overlays</li>
    <li>Process Development and Testing</li>
  </ul>

  <div class="promo">
    <p class="promo-text">With BrisaLink, Velmora Tech’s cloud based inventory and order processing system, you’ll have unprecedented real-time access to your critical order and inventory data</p>
    <div class="promo-button">KNOW MORE</div>
    <div class="promo-devices" role="img" aria-label="Phone, tablet and desktop monitor showing the BrisaLink inventory dashboard"></div>
  </div>

  <footer class="site-footer">
    <nav class="footer-nav">
      Home<span class="sep">|</span>USA Facilities<span class="sep">|</span>China Facilities<span class="sep">|</span>Enclosures<span class="sep">|</span>Antennas<span class="sep">|</span>Connectors<span class="sep">|</span>Cables<span class="sep">|</span>EMI Shields<span class="sep">|</span>Overlays<span class="sep">|</span>Process Development<span class="sep">|</span>BrisaLink<span class="sep">|</span>Contact Us
    </nav>
    <p class="copyright">Copyright © 2013 &nbsp;Velmora Tech. &nbsp;&nbsp;All rights reserved.</p>
    <div class="social"><span></span><span></span><span></span></div>
  </footer>
</body>
</html>
```